A Techincal Author needs a site to promote his Programming Books

The StudyAlong series is a collection of books focusing on building the same app with different technologies. The purpose of this project is to design a web site home page that can be used to sell the books.

Expected Deliverables
• StudyAlong Logo as Illustrator file
• Master graphic design files for any relevant web assets
• HTML and CSS for home page, if applicable

Target Market(s)

The target market for our series is web programmers. They are people who have some experience, but want to learn a new tool. Programmers are analytical, logical people who like structure in the things they do.

Here are some things our customers like:

• Chirply / Postbox
• Crown of Ashes / Hollow Tide / Salt Hollow
• SmartPhones, Tablets, Stridelets, and other tech gadgets.

The design should try to speak to that market.

Requirements
Must have
• The primary tasks for this project are:
• 1) Create "Study Along" Logo.
• * All “NetPivot” properties use a similar logo approach, with the NetPivot ball icon on the left, a reflection below it. The company name is on the right, roughly the same size as the ball icon. A tag line underneath the company name, roughly the same size as the reflection.
• * Company Name: Study Along
• * Tagline: Knowledge to Boost Your Career
• * Logo color is up to the discretion of the designer, but should be compatible with the site design.
• * Sample Logos for other NetPivot properties in Illustrator format are available as attachments to this project.
• 2) Design the Study Along Home Page.
• The home page should follow this format:
• * Logo
• * Nav Bar
• • Buy (The Home Page)
• • About
• • Contact
• * Main Content
• • Home page content detailed in attachment
• * Footer
• • Copyright notice
• • Links to other stuff we do ( net-pivot.example | marlonpeake.example | BeyondTheGrid.example )
Nice to have
• It would be nice to have a book as part of the home page content.
Should not have
• Please do not use the same color scheme as BeyondTheGrid.example or Plumvane.example or QueryTheMaven.example

```html
<!DOCTYPE html>
<html lang="en">
<head>
<meta charset="utf-8">
<title>Study Along — Programming Books</title>
<link href="https://fonts.googleapis.com/css2?family=Open+Sans:wght@400;600;700;800&display=swap" rel="stylesheet">
<style>
:root{
  --red:#a01d22;
  --red-dark:#7e1418;
  --ink:#222;
  --text:#555;
  --muted:#888;
  --line:#e2e2e2;
  --panel:#f4f4f4;
  --bar:#2b2b2b;
  --orange:#f39c12;
  --green:#27ae60;
  --white:#fff;
}
*{box-sizing:border-box;margin:0;padding:0}
html,body{width:1200px;height:2192px;overflow:hidden}
body{font-family:"Open Sans",Arial,sans-serif;color:var(--text);background:var(--white);font-size:11px;position:relative}
.wrap{width:960px;margin:0 auto;position:relative}

/* top bar */
.topbar{height:24px;background:var(--red);color:var(--white);font-size:9px}
.topbar .wrap{display:flex;justify-content:space-between;align-items:center;height:24px}
.topbar .links{display:flex;gap:14px}

/* header */
.site-header{height:60px}
.site-header .wrap{display:flex;align-items:center;justify-content:space-between;height:60px}
.logo{display:flex;align-items:center;gap:8px;font-weight:800;font-size:22px;color:var(--ink)}
.logo .dot{width:14px;height:14px;background:var(--red);border-radius:50%}
.tools{display:flex;align-items:center;gap:8px}
.search{display:flex;width:190px;height:20px;border:1px solid var(--line)}
.search span{flex:1}
.search b{width:22px;background:var(--red);display:flex;align-items:center;justify-content:center}
.cart{display:flex;align-items:center;gap:4px;font-size:9px;color:var(--ink)}

/* nav */
.main-nav{height:24px;border-top:1px solid var(--line);border-bottom:1px solid var(--line)}
.main-nav .wrap{display:flex;align-items:center;height:22px;gap:22px;font-size:9px;color:var(--ink);font-weight:600}

/* hero */
.hero{height:264px;position:relative;background:linear-gradient(180deg,#c9d6e0 0%,#e3e6e4 45%,#b9a48d 70%,#8f8576 100%)}
.hero .stack{position:absolute;right:120px;top:20px;width:230px;height:230px;background:linear-gradient(180deg,#d9d9d9 0%,#6fb7e0 35%,#f2c94c 55%,#e24c4c 75%,#6ac06a 100%);opacity:.9}
.hero .caption{position:absolute;left:240px;top:170px;color:var(--white);font-weight:800;font-size:19px;line-height:24px;letter-spacing:.5px}
.hero .caption span{display:block;background:rgba(160,29,34,.85);padding:0 8px;width:max-content}
.hero .caption span+span{background:rgba(30,30,30,.75)}
.arrow{position:absolute;top:64px;width:30px;height:30px;background:var(--bar);display:flex;align-items:center;justify-content:center}
.arrow.prev{left:180px}.arrow.next{left:990px}

/* welcome */
.welcome{padding:40px 0 0}
.welcome .wrap{display:flex;justify-content:center;gap:30px;align-items:flex-start}
.welcome h2{font-size:15px;font-weight:700;color:var(--ink);line-height:18px;text-align:right}
.welcome h2 em{display:block;font-style:normal;font-weight:800;font-size:14px}
.welcome p{width:300px;font-size:9px;line-height:13px;color:var(--muted)}

/* feature tiles */
.tiles{margin-top:50px}
.tiles .wrap{display:flex;justify-content:center;gap:12px}
.tile{width:236px;height:176px;flex:none}
.tile.promo{background:linear-gradient(135deg,#c8444a,#8e1a1f);color:var(--white);font-size:9px;font-weight:700;text-align:center;padding-top:40px;line-height:13px}
.tile.desk{background:linear-gradient(135deg,#4a3a34 0%,#b98f7d 60%,#d8c6b8 100%)}
.tile.study{background:linear-gradient(135deg,#eae6df 0%,#c9c0b3 60%,#8e857a 100%)}

/* products */
.shelf{margin-top:30px;border:1px solid var(--line);height:320px}
.shelf+.shelf{margin-top:20px}
.shelf-head{display:flex;justify-content:space-between;align-items:center;height:30px;padding:0 12px;font-size:10px;font-weight:700;color:var(--ink);border-bottom:1px solid var(--line)}
.shelf-head small{font-size:8px;color:var(--muted);font-weight:600}
.grid{display:flex;justify-content:center;gap:40px;padding-top:18px}
.card{width:190px;text-align:center;border:1px solid var(--line);height:255px;position:relative}
.cover{height:170px;margin:10px 35px 0}
.tag{position:absolute;top:6px;right:6px;color:var(--white);font-size:7px;font-weight:700;padding:1px 5px}
.tag.sale{background:var(--orange)}.tag.new{background:var(--green)}
.buybar{display:flex;height:20px;background:var(--bar);margin-top:10px;font-size:7px;color:var(--white);align-items:center}
.buybar b{background:var(--red);height:100%;padding:0 8px;display:flex;align-items:center}
.card h3{font-size:9px;font-weight:700;color:var(--ink);margin-top:8px}
.card .price{color:var(--red);font-weight:700;font-size:10px;margin-top:3px}

/* signup */
.signup{margin-top:24px;background:var(--red);height:56px}
.signup .wrap{display:flex;align-items:center;height:56px;gap:10px;color:var(--white)}
.signup h4{font-size:14px;font-weight:600;width:380px}
.signup .field{width:180px;height:22px;background:var(--white);color:var(--muted);font-size:8px;padding:5px}
.signup .go{width:90px;height:22px;background:var(--bar);font-size:8px;font-weight:700;display:flex;align-items:center;justify-content:center}

/* footer */
.site-footer{background:var(--panel);height:260px;padding-top:20px}
.cols{display:flex;gap:30px}
.col{width:220px;font-size:8px;line-height:13px;color:var(--muted)}
.col h5{font-size:9px;color:var(--ink);font-weight:700;margin-bottom:6px;text-transform:uppercase}
.col ul{list-style:none}
.cols+.cols{margin-top:18px}
.faces{display:grid;grid-template-columns:repeat(4,34px);gap:4px}
.faces i{height:34px;background:linear-gradient(135deg,#b7a394,#6b5d52);display:block}
.partners{display:grid;grid-template-columns:repeat(2,70px);gap:6px}
.partners i{height:26px;background:#d6d6d6;display:block}
.social{display:flex;gap:6px}
.social i{width:14px;height:14px;border-radius:50%;background:#9a9a9a;display:block}

.bottom{height:52px;background:var(--white);border-top:1px solid var(--line)}
.bottom .wrap{display:flex;justify-content:space-between;align-items:center;height:52px;font-size:8px;color:var(--muted)}
.cards{display:flex;gap:4px}
.cards i{width:26px;height:16px;background:#cfcfcf;border-radius:2px;display:block}

.float-share{position:absolute;right:4px;top:660px;display:flex;flex-direction:column;gap:6px}
.float-share i{width:14px;height:14px;border-radius:50%;background:#4caf50;display:block}
</style>
</head>
<body>

<div class="topbar"><div class="wrap">
  <span>hello@studyalong.example</span>
  <nav class="links"><span>Wishlist</span><span>My Account</span><span>Checkout</span><span>Log In</span><span>Create Account</span><span>USD</span></nav>
</div></div>

<header class="site-header"><div class="wrap">
  <div class="logo"><span class="dot"></span>Study Along</div>
  <div class="tools">
    <div class="search"><span></span><b><svg width="10" height="10" viewBox="0 0 10 10"><circle cx="4" cy="4" r="3" fill="none" stroke="#fff" stroke-width="1.4"/><line x1="6.2" y1="6.2" x2="9" y2="9" stroke="#fff" stroke-width="1.4"/></svg></b></div>
    <div class="cart"><svg width="14" height="12" viewBox="0 0 14 12"><path d="M1 1h2l2 7h7l1-5H4" fill="none" stroke="#a01d22" stroke-width="1.4"/><circle cx="6" cy="10.5" r="1" fill="#a01d22"/><circle cx="11" cy="10.5" r="1" fill="#a01d22"/></svg>$0.00</div>
  </div>
</div></header>

<nav class="main-nav"><div class="wrap">
  <svg width="11" height="10" viewBox="0 0 11 10"><path d="M5.5 0L0 5h1.5v5h3V7h2v3h3V5H11z" fill="#222"/></svg>
  <span>About us</span><span>Products</span><span>Gallery</span><span>Blog</span><span>Testimonials</span><span>Contact us</span>
</div></nav>

<section class="hero">
  <div class="stack" role="img" aria-label="Photo of a tablet resting on a stack of colourful books above a hazy city"></div>
  <div class="arrow prev"><svg width="10" height="12" viewBox="0 0 10 12"><path d="M7 1L2 6l5 5" fill="none" stroke="#fff" stroke-width="2"/></svg></div>
  <div class="arrow next"><svg width="10" height="12" viewBox="0 0 10 12"><path d="M3 1l5 5-5 5" fill="none" stroke="#fff" stroke-width="2"/></svg></div>
  <div class="caption"><span>KNOWLEDGE TO</span><span>BOOST YOUR CAREER</span></div>
</section>

<section class="welcome"><div class="wrap">
  <h2>WELCOME TO THE<em>Study Along</em></h2>
  <p>Each book in the series builds the same application with a different technology, so you can compare tools side by side. Learn at your own pace, follow clear steps and bring new skills to your next project today.</p>
</div></section>

<section class="tiles"><div class="wrap">
  <div class="tile promo">LEARN WHAT YOU NEED<br>FOR YOUR NEXT PROJECT</div>
  <div class="tile desk" role="img" aria-label="Photo of hands typing on a laptop at a desk"></div>
  <div class="tile study" role="img" aria-label="Photo of a student reading at a bright desk"></div>
</div></section>

<div class="wrap">
  <section class="shelf">
    <div class="shelf-head">ArcScript 1.5 Scaffold<small>View All</small></div>
    <div class="grid">
      <article class="card"><span class="tag sale">SALE</span><div class="cover" role="img" aria-label="Book cover, dark blue" style="background:linear-gradient(160deg,#3a3a3a,#111)"></div><div class="buybar"><b>ADD TO CART</b></div><h3>With HTML Services</h3><p class="price">$4.99</p></article>
      <article class="card"><span class="tag new">NEW</span><div class="cover" role="img" aria-label="Book cover, dark with green accents" style="background:linear-gradient(160deg,#2f3b2f,#111)"></div><div class="buybar"><b>ADD TO CART</b></div><h3>With Nodewright Services</h3><p class="price">$4.99</p></article>
      <article class="card"><span class="tag sale">SALE</span><div class="cover" role="img" aria-label="Book cover, dark with red accents" style="background:linear-gradient(160deg,#3b2a2a,#111)"></div><div class="buybar"><b>ADD TO CART</b></div><h3>With FrostForge Services</h3><p class="price">$4.99</p></article>
      <article class="card"><div class="cover" role="img" aria-label="Bundle of book covers" style="background:linear-gradient(160deg,#2a2f3b,#111)"></div><div class="buybar"><b>ADD TO CART</b></div><h3>Buy Them All</h3><p class="price">$9.99</p></article>
    </div>
  </section>

  <section class="shelf">
    <div class="shelf-head">ArcScript 2 Scaffold<small>View All</small></div>
    <div class="grid">
      <article class="card"><span class="tag sale">SALE</span><div class="cover" role="img" aria-label="Book cover, orange tones" style="background:linear-gradient(160deg,#f0a23a,#7a3d10)"></div><div class="buybar"><b>ADD TO CART</b></div><h3>With HTML Services</h3><p class="price">$4.99</p></article>
      <article class="card"><span class="tag new">NEW</span><div class="cover" role="img" aria-label="Book cover, purple and pink tones" style="background:linear-gradient(160deg,#b04a8c,#3a1a4a)"></div><div class="buybar"><b>ADD TO CART</b></div><h3>With Nodewright Services</h3><p class="price">$4.99</p></article>
      <article class="card"><span class="tag sale">SALE</span><div class="cover" role="img" aria-label="Book cover, warm sunset tones" style="background:linear-gradient(160deg,#e6784a,#5a2a1a)"></div><div class="buybar"><b>ADD TO CART</b></div><h3>With FrostForge Services</h3><p class="price">$4.99</p></article>
      <article class="card"><div class="cover" role="img" aria-label="Bundle of book covers" style="background:linear-gradient(160deg,#c46a3a,#3a2a4a)"></div><div class="buybar"><b>ADD TO CART</b></div><h3>Buy Them All</h3><p class="price">$9.99</p></article>
    </div>
  </section>

  <section class="shelf">
    <div class="shelf-head">Vellum JS<small>View All</small></div>
    <div class="grid">
      <article class="card"><span class="tag sale">SALE</span><div class="cover" role="img" aria-label="Book cover, purple tones" style="background:linear-gradient(160deg,#8a5ab8,#2a1a3a)"></div><div class="buybar"><b>ADD TO CART</b></div><h3>With HTML Services</h3><p class="price">$4.99</p></article>
      <article class="card"><span class="tag new">NEW</span><div class="cover" role="img" aria-label="Book cover, brown tones" style="background:linear-gradient(160deg,#a0703a,#3a2410)"></div><div class="buybar"><b>ADD TO CART</b></div><h3>With Nodewright Services</h3><p class="price">$4.99</p></article>
      <article class="card"><span class="tag sale">SALE</span><div class="cover" role="img" aria-label="Book cover, grey and white tones" style="background:linear-gradient(160deg,#d8d8d8,#5a5a5a)"></div><div class="buybar"><b>ADD TO CART</b></div><h3>With FrostForge Services</h3><p class="price">$4.99</p></article>
      <article class="card"><div class="cover" role="img" aria-label="Bundle of book covers" style="background:linear-gradient(160deg,#6a4a8a,#2a2a2a)"></div><div class="buybar"><b>ADD TO CART</b></div><h3>Buy Them All</h3><p class="price">$9.99</p></article>
    </div>
  </section>
</div>

<section class="signup"><div class="wrap">
  <h4>Sign up for a Free Sample</h4>
  <div class="field">Name</div><div class="field">Email</div><div class="go">SUBMIT</div>
</div></section>

<footer class="site-footer"><div class="wrap">
  <div class="cols">
    <div class="col"><h5>About us</h5><p>Study Along books teach one app built with many tools. Written for working developers who want a clear, structured path to a new technology.</p></div>
    <div class="col"><h5>Information</h5><ul><li>Our Story</li><li>Delivery</li><li>Privacy Policy</li><li>Terms of Use</li><li>Returns</li><li>Site Map</li></ul></div>
    <div class="col"><h5>Pageline</h5><div class="faces" role="img" aria-label="Grid of reader profile photos"><i></i><i></i><i></i><i></i><i></i><i></i><i></i><i></i></div></div>
    <div class="col"><h5>Our partners</h5><div class="partners"><i></i><i></i><i></i><i></i></div></div>
  </div>
  <div class="cols">
    <div class="col"><h5>Information</h5><ul><li>Order History</li><li>Wish List</li><li>Newsletter</li></ul></div>
    <div class="col"><h5>Catalog</h5><ul><li>New Books</li><li>Bundles</li><li>Specials</li></ul></div>
    <div class="col"><h5>Links</h5><ul><li>net-pivot.example</li><li>marlonpeake.example</li><li>BeyondTheGrid.example</li></ul></div>
    <div class="col"><h5>Contact</h5><div class="social"><i></i><i></i><i></i><i></i><i></i></div></div>
  </div>
</div></footer>

<div class="bottom"><div class="wrap">
  <span>© 2016 Study Along. All Rights Reserved.</span>
  <div class="cards"><i></i><i></i><i></i><i></i><i></i></div>
</div></div>

<div class="float-share"><i></i><i></i><i></i></div>

</body>
</html>
```